BrivoTerna. Lantern of the Steady Harvest. Business card

Professional business card for BrivoTerna (Lantern of the Steady Harvest)
My rationale: Strategy-> Execution-> Results-> Value that lead to the BrivoTerna name: We put the Lantern of the Steady Harvest.
We deliver value to our customers helping them at defining a good strategy (cyan arrow). 90% of well formulated strategies fail due to poor execution so we also consider strategical execution very important (green arrow). Due to the execution we obtain the results (blue arrow). Finally, the results provide feedback to redefine strategy, and the new strategy has to be executed and new results obtained providing new feedback and on and on. It's like a wheel that finally, must create corporate value: value for shareholders, staholders, employees, providers...-

Target Market(s)

CEOs and steering comitees , invewrnent funds

Industry/Entity Type

Business Consultant

Contact Information for Business Card

Teodoro Vinsquel
CEO & Founder
teodoro.vinsquel@brivoterna-example.com
Mobile: +34 655.803.912
www.brivoterna-example.com

Colors

Designer to choose colors to be used in the design.

Requirements
Nice to have
• Nice to hace the words: Strategy, execution, results
• Nice to vave the claim: Lantern of the Steady Harvest
• The three colors should be shown:
• cyan for STRATEGY
• green for EXECUTION
• blue for RESULTS
Should not have
• Complete black background

```html
<!DOCTYPE html>
<html lang="en">
<head>
<meta charset="utf-8">
<title>BrivoTerna – Business Card</title>
<link rel="stylesheet" href="https://fonts.googleapis.com/css2?family=Open+Sans:wght@400;600;700;800&display=swap">
<style>
  :root {
    --navy: #0b2f8f;
    --cyan: #1eb4ea;
    --green: #8cc63f;
    --ink: #333a44;
    --paper: #ffffff;
    --backdrop: #e4e6ea;
  }
  * { box-sizing: border-box; margin: 0; padding: 0; }
  html, body {
    width: 1200px;
    height: 900px;
    overflow: hidden;
    background: var(--backdrop);
    font-family: "Open Sans", Arial, sans-serif;
  }
  .card {
    position: absolute;
    width: 560px;
    height: 320px;
    background: var(--paper);
    border-radius: 16px;
    overflow: hidden;
    box-shadow: 0 6px 18px rgba(0, 0, 0, 0.12);
  }
  .card--front { left: 70px; top: 100px; }
  .card--back { left: 570px; top: 480px; }

  .brand-name {
    position: absolute;
    color: var(--navy);
    font-weight: 800;
    letter-spacing: -0.5px;
    line-height: 1;
  }
  .card--front .brand-name { left: 40px; top: 72px; font-size: 44px; }
  .card--back .brand-name {
    left: 0; right: 0; top: 50%;
    transform: translateY(-50%);
    text-align: center;
    font-size: 66px;
  }

  .holder {
    position: absolute;
    right: 40px;
    top: 38px;
    text-align: right;
  }
  .holder__name { color: var(--navy); font-weight: 700; font-size: 21px; }
  .holder__role { color: var(--ink); font-size: 13px; margin-top: 2px; }

  .contact {
    position: absolute;
    left: 40px;
    top: 140px;
    list-style: none;
    color: var(--ink);
    font-size: 13.5px;
    line-height: 22px;
  }
  .contact__item { display: flex; align-items: center; gap: 8px; }
  .contact__icon { width: 12px; height: 12px; flex: none; }
  .contact__web { padding-left: 20px; letter-spacing: 1px; }
  .contact__web strong { color: var(--navy); font-weight: 700; }

  .ribbon { position: absolute; left: 0; bottom: 0; width: 560px; height: 100px; }
  .ribbon text { font-family: "Open Sans", Arial, sans-serif; }
  .ribbon .tagline { fill: var(--paper); font-size: 14px; }
  .ribbon .step-label { fill: var(--paper); font-size: 12.5px; font-weight: 700; letter-spacing: 0.2px; text-anchor: middle; }
</style>
</head>
<body>

<section class="card card--front" aria-label="Business card front">
  <div class="brand-name">BrivoTerna</div>

  <div class="holder">
    <div class="holder__name">Teodoro Vinsquel</div>
    <div class="holder__role">CEO &amp; Founder</div>
  </div>

  <ul class="contact">
    <li class="contact__item">
      <svg class="contact__icon" viewBox="0 0 12 12" aria-hidden="true">
        <rect x="2.5" y="0.5" width="7" height="11" rx="1.5" fill="none" stroke="var(--navy)" stroke-width="1.3"/>
        <rect x="5" y="9" width="2" height="1" fill="var(--navy)"/>
      </svg>
      <span>+34 655.803.912</span>
    </li>
    <li class="contact__item">
      <svg class="contact__icon" viewBox="0 0 12 12" aria-hidden="true">
        <rect x="0.5" y="2" width="11" height="8" rx="1" fill="var(--navy)"/>
        <path d="M1 2.8 L6 6.8 L11 2.8" fill="none" stroke="#fff" stroke-width="1"/>
      </svg>
      <span>teodoro.vinsquel@brivoterna-example.com</span>
    </li>
    <li class="contact__web">www.<strong>brivoterna-example</strong>.com</li>
  </ul>

  <svg class="ribbon" viewBox="0 0 560 100" role="presentation">
    <path d="M0 70 H250 C282 70 282 10 316 10 H560 V100 H0 Z" fill="var(--navy)"/>
    <path d="M322 18 H402 L390 58 H310 Z" fill="var(--cyan)"/>
    <path d="M406 18 H496 L484 58 H394 Z" fill="var(--green)"/>
    <text class="tagline" x="30" y="90">Lantern of the Steady Harvest</text>
    <text class="step-label" x="356" y="43">STRATEGY</text>
    <text class="step-label" x="445" y="43">EXECUTION</text>
    <text class="step-label" x="522" y="43">RESULTS</text>
  </svg>
</section>

<section class="card card--back" aria-label="Business card back">
  <div class="brand-name">BrivoTerna</div>
</section>

</body>
</html>
```